TK Stationery - Modern Contemporary

Develop modern template for Letterhead and Stationery (business card, letterhead, envelopes) using the TK Logo and Icon

Colors
0054AA
0677BA
7BADD7
CADEEF
E8F1F8
00AB8E
00BBA5
67D7C9
C6EFE9
E9F9F6
EE7325
F08F49
F5BC92
FAE3D3
FDF4ED
6B429C
8869AF
B7A5CE
E3DAEB
F3F0F8

```html
<!DOCTYPE html>
<html lang="en">
<head>
<meta charset="utf-8">
<title>TK Stationery Letterhead</title>
<link href="https://fonts.googleapis.com/css2?family=Arimo:wght@400;700&family=Mulish:wght@600;700&display=swap" rel="stylesheet">
<style>
:root{
  --backdrop:#cdcccd;
  --paper:#ffffff;
  --navy:#262c48;
  --green:#3db274;
  --orange:#ee7325;
  --body-text:#4d4d4f;
  --signature-tone:#d9d9db;
}
*{margin:0;padding:0;box-sizing:border-box}
html,body{width:1173px;height:1200px;overflow:hidden;background:var(--backdrop)}
.letterhead{
  position:absolute;left:230px;top:95px;width:713px;height:1010px;overflow:hidden;
  background:var(--paper);font-family:"Arimo",Arial,sans-serif;color:var(--body-text);
}
.brand{
  position:absolute;left:63px;top:58px;display:flex;align-items:center;gap:6px;
  font-family:"Mulish",sans-serif;font-weight:700;font-size:29px;color:var(--navy);letter-spacing:-0.3px;
}
.brand-dot{width:7px;height:7px;border-radius:50%;background:var(--orange);margin-top:-14px}
.divider{position:absolute;top:62px;width:1.5px;height:30px;background:var(--navy)}
.divider-contact{left:329px}
.divider-address{left:528px}
.contact{position:absolute;left:360px;top:62px;font-size:12px;line-height:14.5px;color:var(--navy)}
.contact-row{display:flex;align-items:center;gap:7px}
.contact-row svg{width:9px;height:9px;flex:none}
.address{position:absolute;left:555px;top:62px;font-size:12px;line-height:14.5px;color:var(--navy);font-style:normal}
.header-rule{position:absolute;left:63px;top:102px;width:586px;height:1.5px;background:var(--navy)}
.salutation{
  position:absolute;left:65px;top:311px;font-family:"Mulish",sans-serif;font-weight:700;font-size:16.5px;color:var(--body-text);
}
.letter-body{position:absolute;left:63px;top:358px;width:600px;font-size:12px;line-height:14.8px;white-space:nowrap}
.letter-body p+p{margin-top:12.2px}
.closing{position:absolute;left:65px;top:656px;font-family:"Mulish",sans-serif;font-weight:700;font-size:9.5px}
.signature{position:absolute;left:64px;top:703px;width:117px;height:35px;background:var(--signature-tone);border-radius:3px}
.footer-band{
  position:absolute;left:0;bottom:0;width:713px;height:26px;background:var(--green);
  display:flex;align-items:center;justify-content:flex-end;padding-right:60px;
}
.website{font-weight:700;font-size:14px;color:var(--paper);letter-spacing:0.2px}
</style>
</head>
<body>
<main class="letterhead">
  <header>
    <div class="brand"><span>TK Stationery</span><span class="brand-dot"></span></div>
    <div class="divider divider-contact"></div>
    <div class="contact">
      <div class="contact-row">
        <svg viewBox="0 0 10 10" aria-hidden="true"><path d="M2 1 L3.6 2.8 L2.8 3.8 Q4 6 6.2 7.2 L7.2 6.4 L9 8 L8 9.2 Q4 9 1 5 Q0.8 2 2 1Z" fill="#3db274"/></svg>
        <span>555-014-2780</span>
      </div>
      <div class="contact-row">
        <svg viewBox="0 0 10 10" aria-hidden="true"><rect x="0.5" y="2" width="9" height="6.5" fill="#3db274"/><path d="M0.5 2 L5 5.8 L9.5 2" stroke="#fff" stroke-width="0.9" fill="none"/></svg>
        <span>info@tkstationery.com</span>
      </div>
    </div>
    <div class="divider divider-address"></div>
    <address class="address">Your address, city<br>state, ZIP 0000</address>
    <div class="header-rule"></div>
  </header>

  <h1 class="salutation">Dear Mr. Harlow,</h1>

  <section class="letter-body">
    <p>Lorem ipsum dolor sit amet, consectetuer adipiscing elit, sed diam nonmmy nibh euismod tincidunt ut laor<br>eet dolore magna aliquam erat volutpat. Ut wisi enim ad minim veniam, quis nostrud exerci tationmcorper<br>suscipit lobortis nisl ut aliquip ex ea commodo consequat. Duis autem vel eum iriure dolor in hendrerit in<br>vulputate velit esse molestie consequat, vel illum dolore eu feugiat</p>
    <p>Rorem ipsum dolor sit amet, consectetuer adipiscing elit, sed diam nonmmy nibh euismod tincidunt ut laor<br>eet dolore magna aliquam erat volutpat. Ut wisi enim ad minim veniam, quis nostrud exerci tationmcorper<br>suscipit lobortis nisl ut aliquip ex ea commodo consequat. Duis autem vel eum iriure dolor in hendrerit in<br>vulputate velit esse molest</p>
    <p>Dorem ipsum dolor sit amet, consectetuer adipiscing elit, sed diam nonmmy nibh euismod tincidunt ut laor<br>eet dolore magna aliquam erat volutpat. Ut wisi enim ad minim veniam, quis nostrud exerci tationmcorper<br>suscipit lobortis nisl ut aliquip ex ea commodo consequat. Duis autem vel eum iriure dolor in hendrerit in<br>suscipit lobortis nisl ut aliquip ex ea commodo consequat. Duis autem vel eum iriure dolor in hendrerit in<br>vulputate velit esse molestie consequat, vel illum</p>
    <p>Sorem ipsum dolor sit amet, consectetuer adipiscing elit, sed diam nonmmy nibh euismod tincidunt ut laor<br>eet dolore magna aliquam erat volutpat. Ut wisi enim ad minim veniam, quis nostrud exerci tationmcorper<br>suscipit lobortis nisl ut aliquip ex ea commodo consequat. Duis autem vel eum iriure dolor in</p>
  </section>

  <p class="closing">Sincerely,</p>
  <div class="signature" role="img" aria-label="Handwritten signature of the sender"></div>

  <footer class="footer-band">
    <span class="website">www.tkstationery.com</span>
  </footer>
</main>
</body>
</html>
```